Alberta, Canada based Environmental Oilfield Consultant need a Business Card Design

We need a business card design for a year old company based in Edmonton, Alberta, Canada called Cindermoor Consulting Inc. We are environmental consultants primarily for oilfield based companies (pipeline cleanup, site consultations, environmental site training, and site evaluations).

We like the color blue or green, something very clean and crisp looking.
We don't really care if there is an otter on it but most of our work is land based and nothing really to do with oceans or larger bodies of water.

The name Cindermoor was the name of our fathers boat, and named our company that in his memory.

```html
<!DOCTYPE html>
<html lang="en">
<head>
<meta charset="utf-8">
<title>Cindermoor Consulting Inc. — Business Card</title>
<link href="https://fonts.googleapis.com/css2?family=Exo+2:wght@400;500;800&display=swap" rel="stylesheet">
<style>
  :root{
    --backdrop:#e9e7e4;
    --card-top:#ffffff;
    --card-bottom:#e6e6e6;
    --ink:#2f2f2f;
    --ink-soft:#4a4a4a;
    --brand:#5d5d5d;
    --accent-light:#ffb640;
    --accent-dark:#f28a12;
  }
  *{margin:0;padding:0;box-sizing:border-box}
  html,body{width:1200px;height:892px;overflow:hidden}
  body{
    background:var(--backdrop);
    display:flex;align-items:center;justify-content:center;
    font-family:"Exo 2",Arial,sans-serif;
  }
  .business-card{
    position:relative;width:840px;height:480px;
    background:linear-gradient(160deg,var(--card-top) 0%,#f6f6f6 55%,var(--card-bottom) 100%);
    box-shadow:0 14px 40px rgba(0,0,0,.18);
    overflow:hidden;
  }
  .accent-block{
    position:absolute;left:60px;bottom:0;width:120px;height:62px;
    background:linear-gradient(135deg,var(--accent-light),var(--accent-dark));
  }
  .brand-name{
    position:absolute;right:44px;top:46px;
    font-weight:800;font-size:50px;line-height:1.02;
    color:var(--brand);text-align:left;letter-spacing:1px;
  }
  .holder{position:absolute;left:54px;top:196px;color:var(--ink)}
  .holder-name{font-size:25px;font-weight:500;letter-spacing:1.5px}
  .holder-title{font-size:15px;letter-spacing:1.5px;color:var(--ink-soft);margin-top:2px}
  .address{position:absolute;left:54px;top:272px;font-size:17px;line-height:1.3;color:var(--ink);letter-spacing:.5px}
  .contact-list{position:absolute;left:54px;top:334px;list-style:none;font-size:14px;color:var(--ink);letter-spacing:.5px}
  .contact-list li{display:flex;align-items:center;gap:10px;height:17px}
  .contact-list svg{width:12px;height:12px;fill:var(--ink-soft)}
</style>
</head>
<body>
  <article class="business-card">
    <div class="brand-name">Cindermoor<br>Consulting</div>

    <div class="holder">
      <div class="holder-name">ALAN REEVE</div>
      <div class="holder-title">GENERAL MANAGER</div>
    </div>

    <address class="address" style="font-style:normal">
      214 Birch Hollow Road,<br>2nd building Street E.
    </address>

    <ul class="contact-list">
      <li><svg viewBox="0 0 12 12" aria-hidden="true"><path d="M2.5 1l2 2.2-1 1.3c.7 1.5 1.7 2.5 3.1 3.1l1.3-1L10.9 8.6 9.6 11C5.4 10.6 1.4 6.6 1 2.4z"/></svg>012 555 0148</li>
      <li><svg viewBox="0 0 12 12" aria-hidden="true"><path d="M3 0h6v12H3zM4 1.5v8h4v-8z"/></svg>012 555 0172</li>
      <li><svg viewBox="0 0 12 12" aria-hidden="true"><path d="M3 0h5v3H3zM1 4h10v6H1zM3 9h6v3H3z"/></svg>012 555 0193</li>
      <li><svg viewBox="0 0 12 12" aria-hidden="true"><path d="M0 2h12v8H0zM1 3l5 4 5-4v-.2H1z"/></svg>hello@cindermoorco.ca</li>
      <li><svg viewBox="0 0 12 12" aria-hidden="true"><path d="M6 0a6 6 0 100 12A6 6 0 006 0zm0 1c.8.9 1.3 2.2 1.4 3.5H4.6C4.7 3.2 5.2 1.9 6 1zM1.1 5.5h2.5c0 1.3.4 2.5 1 3.5a5 5 0 01-3.5-3.5zm7.3 0h2.5a5 5 0 01-3.5 3.5c.6-1 1-2.2 1-3.5zM4.6 5.5h2.8c-.1 1.4-.6 2.6-1.4 3.5-.8-.9-1.3-2.1-1.4-3.5z"/></svg>www.cindermoorco.ca</li>
    </ul>

    <div class="accent-block"></div>
  </article>
</body>
</html>
```